Design a web site for my business - Brightline Coatings Co.

We are a family business that handles design, fabrication and installation of powder coated aluminum, stainless steel and glass products. Including handrails, privacy slat screens, electric gates and pool fencing. We are based in the Whitsundays in North Queensland and service an area from Airlie Beach to Townsville.

Target Market(s)

Domestic and commercial

Industry/Entity Type

fabrication - manufacturing

Coding

Coded - Design and coding required

Number of Pages Required

5+ page

Colors
0054AA
0677BA
7BADD7
CADEEF
E8F1F8

Requirements
Must have
• photo galleries, contact page, one page for privacy screens, balustrades, glass fencing, stainless steel handrail, powder coated aluminium handrails and pool fencing

```html
<!DOCTYPE html>
<html lang="en">
<head>
<meta charset="utf-8">
<title>Brightline Coatings Co – Option 2</title>
<link href="https://fonts.googleapis.com/css2?family=Figtree:wght@400;500;600;700&display=swap" rel="stylesheet">
<style>
:root{
  --blue-900:#0a3a7a;
  --blue-700:#0054AA;
  --blue-600:#0677BA;
  --blue-300:#7BADD7;
  --blue-200:#CADEEF;
  --blue-100:#E8F1F8;
  --ink:#111827;
  --muted:#4b5563;
  --white:#ffffff;
  --line:#e3e8ef;
}
*{box-sizing:border-box;margin:0;padding:0}
html,body{width:1200px;height:1200px;overflow:hidden}
body{background:var(--blue-200);font-family:"Figtree",sans-serif;color:var(--ink);position:relative}
.abs{position:absolute}
.board-title{left:0;width:630px;top:6px;text-align:center;font-size:19px;font-weight:500}
.page{position:absolute;background:var(--white);overflow:hidden}
.page-left{left:119px;top:47px;width:410px;height:1153px}
.page-right{left:608px;top:0;width:392px;height:1197px}
.eyebrow{font-size:4.6px;font-weight:700;letter-spacing:.4px;color:var(--blue-700);text-transform:uppercase}
.h2{font-size:12px;font-weight:600;line-height:1.1}
.body{font-size:4.6px;line-height:1.65;color:var(--muted)}
.btn{display:flex;align-items:center;justify-content:center;border-radius:8px;font-size:4.4px;font-weight:500}
.btn-primary{background:var(--blue-700);color:var(--white)}
.btn-ghost{background:rgba(255,255,255,.18);color:var(--white)}
.btn-white{background:var(--white);color:var(--ink)}
.photo{border-radius:5px}
/* nav */
.nav{left:0;top:0;width:410px;height:23px;background:var(--white)}
.brand{display:flex;align-items:center;gap:2px;font-size:3.4px;font-weight:600;color:var(--ink)}
.brand i{width:5px;height:5px;background:var(--blue-700);display:block}
.nav-links{left:132px;top:9px;display:flex;gap:11px;font-size:4.6px;font-weight:500}
/* hero */
.hero{left:0;top:23px;width:410px;height:214px;background:linear-gradient(135deg,#4d5c7e 0%,#3e4d6f 50%,#2d3a55 100%)}
.hero h1{left:38px;top:57px;font-size:15px;font-weight:500;line-height:1;color:var(--white)}
.hero p{left:38px;top:97px;font-size:4.9px;line-height:1.35;color:var(--white)}
/* service cards */
.svc{border-radius:5px;overflow:hidden}
.svc .shade{inset:0;background:linear-gradient(90deg,rgba(10,20,35,.75) 0%,rgba(10,20,35,.35) 45%,rgba(10,20,35,0) 75%)}
.svc h3{font-size:12px;font-weight:500;color:var(--white)}
.svc p{font-size:4.6px;line-height:1.55;color:#e5e7eb;width:118px}
.svc .btn{width:27px;height:11px;font-size:4px}
/* feature cards */
.feat{background:var(--white);border-radius:4px;width:76px;height:73px}
.feat .ico{left:6px;top:8px;width:14px;height:14px;border-radius:3px;background:var(--blue-100);display:flex;align-items:center;justify-content:center}
.feat h4{left:6px;top:33px;font-size:5.6px;font-weight:500}
.feat p{left:6px;top:45px;width:64px;font-size:3.9px;line-height:1.4;color:var(--muted)}
/* stats */
.stats{left:0;top:426px;width:392px;height:102px;background:linear-gradient(90deg,#0a62c7 0%,#0677BA 100%);color:var(--white)}
.stat{top:57px}
.stat b{display:block;font-size:11px;font-weight:500}
.stat span{display:block;margin-top:5px;font-size:4.4px}
.divider{top:57px;width:.5px;height:27px;background:rgba(255,255,255,.35)}
/* service list */
.srv-item{left:37px;width:140px;font-size:5.2px;font-weight:500;border-bottom:.5px solid var(--line);padding-bottom:5px}
.srv-item svg{position:absolute;right:0;top:1px}
/* testimonials */
.tcard{top:801px;width:101px;height:116px;background:var(--white);border-radius:4px}
.tcard .q{left:8px;top:12px;font-size:14px;line-height:1;color:var(--blue-300);font-weight:700}
.tcard p{left:8px;top:31px;width:86px;font-size:4.4px;line-height:1.9}
.tcard .avatar{left:8px;top:94px;width:13px;height:13px;border-radius:50%;background:linear-gradient(135deg,#c9b39a,#7d6a58)}
.tcard b{left:29px;top:95px;font-size:5px;font-weight:600}
.tcard small{left:29px;top:102.5px;font-size:3.8px;color:var(--muted)}
/* footer */
.foot-col h5{font-size:4.8px;font-weight:600;margin-bottom:6px}
.foot-col li{list-style:none;font-size:3.7px;color:var(--muted);margin-bottom:5.6px}
.social{width:5px;height:5px;border-radius:50%;background:#d1d5db}
</style>
</head>
<body>

<div class="abs board-title">Option-2</div>

<!-- LEFT PAGE -->
<section class="page page-left">
  <header class="abs nav">
    <div class="abs brand" style="left:38px;top:8px"><i></i>Brightline Coatings Co</div>
    <nav class="abs nav-links"><span>About</span><span>Services</span><span>Projects</span><span>Testimonials</span><span>Contacts</span></nav>
    <div class="abs btn btn-primary" style="left:318px;top:5px;width:54px;height:14px">Get a Free Quote</div>
  </header>

  <div class="abs hero" role="img" aria-label="Modern building corner with glass balustrade, blue-toned overlay">
    <h1 class="abs">Custom Fabrication<br>for Modern Living</h1>
    <p class="abs">Precision-crafted aluminium, stainless steel, and glass solutions<br>for homes and businesses across North Queensland.</p>
    <div class="abs btn btn-primary" style="left:38px;top:115px;width:54px;height:13px">Get a Free Quote</div>
    <div class="abs btn btn-ghost" style="left:97px;top:115px;width:46px;height:13px">View Projects</div>
  </div>

  <!-- about -->
  <div class="abs eyebrow" style="left:38px;top:279px">Crafting Quality That Lasts</div>
  <h2 class="abs h2" style="left:38px;top:288px">Built by Locals for the<br>Unique Whitsunday<br>Environment</h2>
  <p class="abs body" style="left:38px;top:336px;width:132px">At Brightline Coatings Co, we don’t just build enclosures; we engineer structural statements that thrive in harsh coastal conditions. Our family-owned operation bridges the gap between industrial durability and architectural elegance.</p>
  <div class="abs" style="left:38px;top:390px;font-size:4.6px;color:var(--blue-700);border-bottom:.6px solid var(--blue-700);padding-bottom:2px;width:53px">Learn more about us →</div>
  <div class="abs photo" style="left:210px;top:260px;width:162px;height:153px;background:linear-gradient(180deg,#8fbcd9 0%,#4c7a55 45%,#6d6a5e 70%,#a77a4a 100%)" role="img" aria-label="Coastal boardwalk with timber-look railings by rocky shoreline"></div>

  <!-- why us -->
  <div class="abs" style="left:0;top:436px;width:410px;height:200px;background:linear-gradient(180deg,var(--blue-100) 0%,#f4f8fc 80%,var(--white) 100%)"></div>
  <div class="abs eyebrow" style="left:38px;top:462px">Why Choose Us</div>
  <h2 class="abs h2" style="left:38px;top:469px">The Fence Company<br>You Can Rely On</h2>
  <div class="abs photo" style="left:34px;top:509px;width:162px;height:104px;background:linear-gradient(180deg,#2f64b6 0%,#6f9ad2 55%,#d9d8d2 60%,#c7c5bd 100%)" role="img" aria-label="White slatted aluminium gates against a clear blue sky"></div>

  <div class="abs feat" style="left:205px;top:459px">
    <div class="abs ico"><svg width="7" height="7" viewBox="0 0 10 10" fill="none" stroke="#0054AA" stroke-width="1"><rect x="1.5" y="1" width="7" height="4" rx=".6"/><path d="M5 5v4"/></svg></div>
    <h4 class="abs">Custom Designed</h4><p class="abs">Every solution is tailored to match your project and requirements.</p>
  </div>
  <div class="abs feat" style="left:291px;top:459px">
    <div class="abs ico"><svg width="7" height="7" viewBox="0 0 10 10" fill="none" stroke="#0054AA" stroke-width="1"><circle cx="5" cy="2" r="1"/><path d="M5 3L2 9M5 3l3 6M3 6.5h4"/></svg></div>
    <h4 class="abs">Premium Finishes</h4><p class="abs">Durable powder-coated and stainless steel finishes built to last.</p>
  </div>
  <div class="abs feat" style="left:205px;top:540px">
    <div class="abs ico"><svg width="8" height="7" viewBox="0 0 12 10" fill="none" stroke="#0054AA" stroke-width="1"><circle cx="4" cy="3" r="1.5"/><circle cx="8" cy="3" r="1.5"/><path d="M1 9c0-2 1.5-3 3-3s3 1 3 3M5 9c0-2 1.5-3 3-3s3 1 3 3"/></svg></div>
    <h4 class="abs">Experienced Team</h4><p class="abs">Skilled professionals delivering quality craftsmanship from start to finish.</p>
  </div>
  <div class="abs feat" style="left:291px;top:540px">
    <div class="abs ico"><svg width="7" height="7" viewBox="0 0 10 10" fill="none" stroke="#0054AA" stroke-width="1"><rect x="1" y="3" width="8" height="6" rx=".6"/><path d="M3.5 3V1.5h3V3M1 5.5h8"/></svg></div>
    <h4 class="abs">Australian Standards</h4><p class="abs">Designed and installed to meet Australian safety and quality standards.</p>
  </div>

  <!-- core capabilities -->
  <div class="abs eyebrow" style="left:38px;top:655px">Core Capabilities</div>
  <h2 class="abs h2" style="left:38px;top:663px">Specialized<br>Fabrication Services</h2>
  <p class="abs body" style="left:266px;top:663px;width:106px;color:var(--ink)">Providing high-performance architectural metalwork for luxury homes and large-scale commercial developments.</p>

  <div class="abs svc" style="left:38px;top:713px;width:334px;height:142px;background:linear-gradient(120deg,#2a3038 0%,#3f4a3f 55%,#5f7048 100%)" role="img" aria-label="Black laser-cut privacy screen with leaf pattern in a garden">
    <div class="abs shade"></div>
    <h3 class="abs" style="left:17px;top:64px">Privacy Screens</h3>
    <p class="abs" style="left:17px;top:81px">Custom-slatted or decorative laser-cut solutions providing secluded spaces without compromising tropical airflow.</p>
    <div class="abs btn btn-ghost" style="left:17px;top:112px">Learn More</div>
  </div>
  <div class="abs svc" style="left:38px;top:864px;width:334px;height:142px;background:linear-gradient(120deg,#4a5866 0%,#6a7280 45%,#8a4a52 75%,#c9b8a0 100%)" role="img" aria-label="Red metal balustrade on a balcony overlooking a lake town">
    <div class="abs shade"></div>
    <h3 class="abs" style="left:17px;top:64px">Balustrades</h3>
    <p class="abs" style="left:17px;top:81px">Architectural stainless steel, glass, or aluminium balustrades engineered for uncompromising safety and flow.</p>
    <div class="abs btn btn-ghost" style="left:17px;top:112px">Learn More</div>
  </div>
  <div class="abs svc" style="left:38px;top:1015px;width:334px;height:142px;background:linear-gradient(120deg,#2d3a33 0%,#4d5a52 50%,#7b8780 100%)" role="img" aria-label="Frameless glass pool fence on stone coping">
    <div class="abs shade"></div>
    <h3 class="abs" style="left:17px;top:64px">Glass Pool Fencing</h3>
    <p class="abs" style="left:17px;top:81px">Frameless and semi-frameless glass systems that maintain uninterrupted ocean views while exceeding standards.</p>
    <div class="abs btn btn-ghost" style="left:17px;top:112px">Learn More</div>
  </div>
</section>

<!-- RIGHT PAGE -->
<section class="page page-right">
  <div class="abs svc" style="left:37px;top:-27px;width:318px;height:142px;background:linear-gradient(120deg,#2d3a33 0%,#4d5a52 50%,#7b8780 100%)" role="img" aria-label="Frameless glass pool fence on stone coping">
    <div class="abs shade"></div>
    <h3 class="abs" style="left:16px;top:66px">Glass Pool Fencing</h3>
    <p class="abs" style="left:16px;top:83px">Frameless and semi-frameless glass systems that maintain uninterrupted ocean views while exceeding standards.</p>
    <div class="abs btn btn-ghost" style="left:16px;top:114px">Learn More</div>
  </div>
  <div class="abs svc" style="left:37px;top:124px;width:318px;height:136px;background:linear-gradient(110deg,#1e2a2e 0%,#4a4038 40%,#a0603e 60%,#5d7a4a 85%,#b9aa9c 100%)" role="img" aria-label="Automatic gate with timber-look slats beside climbing plants">
    <div class="abs shade"></div>
    <h3 class="abs" style="left:16px;top:61px">Automatic Gates</h3>
    <p class="abs" style="left:16px;top:78px">High-security automated entries with integrated timber-look slats or architectural metal profiles.</p>
    <div class="abs btn btn-ghost" style="left:16px;top:107px">Learn More</div>
  </div>
  <div class="abs svc" style="left:37px;top:263px;width:318px;height:135px;background:linear-gradient(110deg,#1a2426 0%,#2f3a3c 50%,#6d7476 80%,#a3a8a8 100%)" role="img" aria-label="Dark powder-coated sliding door frames on a deck">
    <div class="abs shade"></div>
    <h3 class="abs" style="left:16px;top:61px">Powder Coating</h3>
    <p class="abs" style="left:16px;top:78px">Industrial-grade finishes in over 200+ colors, cured in-house for maximum resistance to UV and salt spray.</p>
    <div class="abs btn btn-ghost" style="left:16px;top:107px">Learn More</div>
  </div>

  <div class="abs stats">
    <h2 class="abs" style="left:0;width:392px;top:22px;text-align:center;font-size:11px;font-weight:600;line-height:1.2">Delivering Quality Without<br>Compromise</h2>
    <div class="abs stat" style="left:66px"><b>500+</b><span>Project Completed</span></div>
    <div class="abs divider" style="left:126px"></div>
    <div class="abs stat" style="left:141px"><b>15+</b><span>Years Experience</span></div>
    <div class="abs divider" style="left:196px"></div>
    <div class="abs stat" style="left:216px"><b>100%</b><span>Customer Satisfaction</span></div>
    <div class="abs divider" style="left:278px"></div>
    <div class="abs stat" style="left:292px"><b>6+</b><span>Core Services</span></div>
  </div>

  <!-- custom solution -->
  <div class="abs eyebrow" style="left:37px;top:555px">Custom Solution</div>
  <h2 class="abs h2" style="left:37px;top:565px">Expert Installation &amp;<br>Repair Service</h2>
  <p class="abs body" style="left:37px;top:597px;width:140px;color:var(--ink)">We provide professional fence installation, repair, and custom solutions to match your style and needs.</p>
  <div class="abs srv-item" style="top:624px">New Fence Installtion<svg width="5" height="5" viewBox="0 0 6 6" fill="none" stroke="#111827" stroke-width=".6"><path d="M1 5L5 1M2 1h3v3"/></svg></div>
  <div class="abs srv-item" style="top:642px;font-size:6.6px;padding-bottom:6px">Fence Repair &amp; Installation<svg width="6" height="5" viewBox="0 0 7 6" fill="none" stroke="#0054AA" stroke-width=".6"><path d="M0 3h6M4 1l2 2-2 2"/></svg>
    <span style="display:block;margin-top:3px;font-size:4.4px;font-weight:400;line-height:1.6;color:var(--muted);width:118px">We fix damaged posts, panels, and gate or replace old fence entirely, to restort security and style.</span></div>
  <div class="abs srv-item" style="top:680px">Custom Gate Installation<svg width="5" height="5" viewBox="0 0 6 6" fill="none" stroke="#111827" stroke-width=".6"><path d="M1 5L5 1M2 1h3v3"/></svg></div>
  <div class="abs srv-item" style="top:698px;border-bottom:none">Fence Maintenance<svg width="5" height="5" viewBox="0 0 6 6" fill="none" stroke="#111827" stroke-width=".6"><path d="M1 5L5 1M2 1h3v3"/></svg></div>
  <div class="abs photo" style="left:200px;top:551px;width:155px;height:159px;background:linear-gradient(170deg,#b9c7a8 0%,#a88a62 35%,#6f5a44 60%,#c9bfae 85%,#8ea06a 100%)" role="img" aria-label="Patio with wicker furniture under a pergola beside a timber fence"></div>

  <!-- testimonials -->
  <div class="abs" style="left:0;top:738px;width:392px;height:207px;background:linear-gradient(180deg,var(--blue-100) 0%,#f3f7fb 85%,var(--white) 100%)"></div>
  <div class="abs eyebrow" style="left:0;width:392px;top:759px;text-align:center">Testimonials</div>
  <h2 class="abs h2" style="left:0;width:392px;top:768px;text-align:center;font-size:11px">What Our Client Says</h2>

  <div class="abs tcard" style="left:37px"><div class="abs q">“</div>
    <p class="abs">The precision Brightline Coatings achieved on our frameless glass balustrades was breathtaking. Their expertise in coastal finishes gave us complete peace of mind for our beachfront build.”</p>
    <div class="abs avatar" role="img" aria-label="Client portrait"></div><b class="abs">Marcus Hale</b><small class="abs">Airlie Beach Developer</small></div>
  <div class="abs tcard" style="left:146px"><div class="abs q">“</div>
    <p class="abs">Unmatched reliability. As a commercial developer, I appreciate their adherence to strict timelines and the superior quality of their automatic gate installations.”</p>
    <div class="abs avatar" role="img" aria-label="Client portrait"></div><b class="abs">Lena Carver</b><small class="abs">Director, LC Construction</small></div>
  <div class="abs tcard" style="left:254px"><div class="abs q">“</div>
    <p class="abs">They transformed our home with custom-designed privacy screens. The powder coat finish is flawless and the installation was incredibly professional.”</p>
    <div class="abs avatar" role="img" aria-label="Client portrait"></div><b class="abs">The Whitfords</b><small class="abs">Hamilton Island Residents</small></div>

  <!-- CTA -->
  <div class="abs" style="left:0;top:945px;width:392px;height:121px;background:linear-gradient(90deg,#1d4f8e 0%,#2c5f95 50%,#3e6f94 100%)" role="img" aria-label="Timber post-and-rail fence across a green field, blue overlay">
    <h2 class="abs" style="left:37px;top:27px;font-size:11px;font-weight:600;line-height:1.1;color:var(--white)">Ready to Start Your<br>Next Project?</h2>
    <p class="abs" style="left:37px;top:58px;font-size:4.6px;line-height:1.5;color:var(--white);width:122px">Supporting text encouraging users to request a free consultation and quote.</p>
    <div class="abs btn btn-white" style="left:37px;top:82px;width:51px;height:12px">Get a Free Quote</div>
    <div class="abs btn btn-ghost" style="left:92px;top:82px;width:31px;height:12px">Call Us</div>
  </div>

  <!-- footer -->
  <footer class="abs" style="left:0;top:1066px;width:392px;height:131px;background:var(--blue-100)">
    <div class="abs brand" style="left:37px;top:21px"><i></i>Brightline Coatings Co</div>
    <p class="abs" style="left:37px;top:44px;width:70px;font-size:3.7px;line-height:1.6;color:var(--muted)">Family-owned specialists delivering custom structural solutions across the Whitsundays. Precision engineered for tropical durability, designed for timeless beauty.</p>
    <div class="abs" style="left:37px;top:81px;display:flex;gap:6px"><span class="social"></span><span class="social"></span><span class="social"></span></div>
    <div class="abs foot-col" style="left:134px;top:21px"><h5>Quick Links</h5><ul><li>About</li><li>Services</li><li>Project</li><li>Testimonials</li><li>Contact us</li></ul></div>
    <div class="abs foot-col" style="left:203px;top:21px"><h5>Services</h5><ul><li>Privacy Screens</li><li>Balustrades</li><li>Glass Pool Fencing</li><li>Automatic Gates</li><li>Powder Coating</li></ul></div>
    <div class="abs foot-col" style="left:276px;top:21px"><h5>Reach us</h5></div>
    <svg class="abs" style="left:276px;top:34px" width="5" height="5" viewBox="0 0 10 10"><rect width="10" height="10" rx="2" fill="#0054AA"/><path d="M2 3.5l3 2 3-2" stroke="#fff" stroke-width="1" fill="none"/></svg>
    <div class="abs" style="left:285px;top:32px;font-size:3.6px;line-height:1.5;color:var(--ink)">48 Forge Street,<br>Cannonvale QLD 4802</div>
    <svg class="abs" style="left:276.5px;top:47px" width="4" height="6" viewBox="0 0 6 10"><rect x=".5" y=".5" width="5" height="9" rx="1" fill="none" stroke="#0054AA" stroke-width="1"/></svg>
    <div class="abs" style="left:285px;top:48px;font-size:3.6px">(07) 5550 1842</div>
    <svg class="abs" style="left:276.5px;top:59px" width="5" height="6" viewBox="0 0 8 10"><path d="M4 10S0 6 0 4a4 4 0 018 0c0 2-4 6-4 6z" fill="#0054AA"/><circle cx="4" cy="4" r="1.3" fill="#fff"/></svg>
    <div class="abs" style="left:285px;top:60px;font-size:3.6px">hello@brightlinecoatings.com.au</div>
    <div class="abs" style="left:0;top:110px;width:392px;height:21px;background:#f3f7fb;border-top:.5px solid var(--line)"></div>
    <div class="abs" style="left:37px;top:118px;font-size:3.6px">© 2024 Brightline Coatings Co. All Rights Reserved.</div>
    <div class="abs" style="left:262px;top:118px;display:flex;gap:11px;font-size:3.6px"><span>Privacy Policy</span><span>Terms of Service</span><span>Sitemap</span></div>
  </footer>
</section>

</body>
</html>
```